Machining Business Order Thank You Insert

I am looking for a business style card to include with orders that I ship. The card needs to thank the recipient for their order, and encourage them to leave a review. The card should include my business name and contact information and have an area to hand write a message.

I mainly sale on Craftlane and my own website. We are a machining an manufacturing business that are in the sale of mostly metal machined and 3d printed plastic products.

The front of the card should include the following:
Logo: (attached)
Snapgram: https://www.snapgram.example/kelvomill/
Friendsbook: https://www.friendsbook.example/KelvoMill
Website: https://www.kelvomill.example/

The back of the card needs an area to write a message

Industry/Entity Type

3D Printing, Machining, Craftlane

Contact Information for Business Card

Black or white front, white back to write a personal message

Font styles to use
Sans Serif

Colors

Designer to choose colors to be used in the design.

Requirements
Must have
• Encourage a review, social media info

```html
<!DOCTYPE html>
<html lang="en">
<head>
<meta charset="utf-8">
<title>KelvoMill – Order Thank You Insert</title>
<link rel="stylesheet" href="https://fonts.googleapis.com/css2?family=Barlow:wght@400;500&family=Barlow+Semi+Condensed:wght@400&display=swap">
<style>
  :root {
    --backdrop: #1b1b1b;
    --paper: #ffffff;
    --orange-light: #f06b44;
    --orange-deep: #eb5529;
    --slate: #6b6b6d;
    --ink-grey: #5d5d60;
    --rule: #6f6f6f;
  }
  * { margin: 0; padding: 0; box-sizing: border-box; }
  html, body { width: 1200px; height: 790px; overflow: hidden; }
  body {
    background: var(--backdrop);
    position: relative;
    font-family: "Barlow", sans-serif;
  }
  .card {
    position: absolute;
    top: 258px;
    width: 480px;
    height: 274px;
    background: var(--paper);
    overflow: hidden;
  }
  .card--front { left: 103px; }
  .card--back { left: 605px; }
  .card__shape { position: absolute; inset: 0; width: 480px; height: 274px; }

  .brand-name {
    position: absolute;
    left: 0; right: 0;
    text-align: center;
    font-family: "Barlow", sans-serif;
    font-weight: 500;
    color: var(--ink-grey);
    letter-spacing: 0.32em;
    padding-left: 0.32em;
    line-height: 1;
  }
  .card--front .brand-name { top: 86px; font-size: 24px; }
  .card--back .brand-name { top: 148px; font-size: 22px; }

  .thanks {
    position: absolute;
    left: 0; right: 0;
    text-align: center;
    color: var(--ink-grey);
    font-family: "Barlow", sans-serif;
    line-height: 1;
  }
  .thanks__title { top: 180px; font-size: 13px; font-weight: 500; color: var(--orange-deep); }
  .thanks__review { top: 198px; font-size: 10.5px; font-weight: 400; }

  .contact {
    position: absolute;
    left: 0; right: 0;
    top: 206px;
    text-align: center;
    color: var(--paper);
    font-family: "Barlow Semi Condensed", sans-serif;
    font-style: normal;
    font-size: 12px;
    line-height: 13.5px;
  }
  .contact__line { display: block; white-space: nowrap; }
  .contact__item { display: inline-flex; align-items: center; gap: 2px; margin: 0 1px; }
  .contact__icon { width: 8px; height: 8px; fill: var(--paper); }

  .message-line {
    position: absolute;
    left: 34px;
    width: 414px;
    border-top: 1px dotted var(--rule);
  }
  .message-line--first { top: 230px; }
  .message-line--second { top: 254px; }
</style>
</head>
<body>

<section class="card card--front" aria-label="Card front with contact details">
  <svg class="card__shape" viewBox="0 0 480 274" aria-hidden="true">
    <defs>
      <linearGradient id="orange-field" x1="0" y1="0" x2="1" y2="1">
        <stop offset="0" stop-color="#f06b44"/>
        <stop offset="1" stop-color="#eb5529"/>
      </linearGradient>
    </defs>
    <polygon points="0,76 240,186 480,76 480,274 0,274" fill="url(#orange-field)"/>
  </svg>

  <div class="brand-name">KELVOMILL</div>

  <address class="contact">
    <span class="contact__line">
      <span class="contact__item">
        <svg class="contact__icon" viewBox="0 0 10 10" aria-hidden="true"><path d="M5 0a3.5 3.5 0 0 0-3.5 3.5C1.5 6 5 10 5 10s3.5-4 3.5-6.5A3.5 3.5 0 0 0 5 0zm0 5a1.4 1.4 0 1 1 0-2.8A1.4 1.4 0 0 1 5 5z"/></svg>
        Maplewood, IN
      </span>
      <span class="contact__item">
        <svg class="contact__icon" viewBox="0 0 10 10" aria-hidden="true"><path d="M2 0l2 2.5-1 1.2a6 6 0 0 0 3.3 3.3l1.2-1L10 8l-1.3 1.6C4.5 10 0 5.5.4 1.3z"/></svg>
        555-014-2283
      </span>
    </span>
    <span class="contact__line">
      <span class="contact__item">
        <svg class="contact__icon" viewBox="0 0 10 10" aria-hidden="true"><path d="M0 2h10v6H0zM.6 2.4 5 5.6l4.4-3.2" stroke="#eb5529" stroke-width=".8"/></svg>
        kelvomillcnc@mail.example
      </span>
      <span class="contact__item">
        <svg class="contact__icon" viewBox="0 0 10 10" aria-hidden="true"><circle cx="5" cy="5" r="4.5"/><path d="M.5 5h9M5 .5c-2 2.5-2 6.5 0 9M5 .5c2 2.5 2 6.5 0 9" stroke="#eb5529" stroke-width=".7" fill="none"/></svg>
        www.kelvomill.example
      </span>
    </span>
    <span class="contact__line">
      <span class="contact__item">
        <svg class="contact__icon" viewBox="0 0 10 10" aria-hidden="true"><circle cx="5" cy="5" r="4.5"/></svg>
        @kelvomill
      </span>
      <span class="contact__item">
        <svg class="contact__icon" viewBox="0 0 10 10" aria-hidden="true"><circle cx="5" cy="5" r="4.5"/></svg>
        /KelvoMill
      </span>
    </span>
  </address>
</section>

<section class="card card--back" aria-label="Card back with thank-you note and space for a handwritten message">
  <svg class="card__shape" viewBox="0 0 480 274" aria-hidden="true">
    <polygon points="0,0 480,0 480,124 240,14 0,124" fill="#6b6b6d"/>
  </svg>

  <div class="brand-name">KELVOMILL</div>
  <p class="thanks thanks__title">Thank you for your order!</p>
  <p class="thanks thanks__review">Enjoying it? Please leave us a review on Craftlane or www.kelvomill.example</p>

  <div class="message-line message-line--first"></div>
  <div class="message-line message-line--second"></div>
</section>

</body>
</html>
```